Professional Baby Bottle Bank Print Design

We need a baby bottle design that is 4.25" wide x 2.28" tall with a maximum of 6 colors (white is counted as a color).

The bottle design needs to be fun but professional. Bottles with cartoon images on it will be rejected immediately.

The bottle design wraps around the bottle. See examples here: https://vel.quin/cat/BabyBottles/HarlowBottles/5

Minimum font size is 10pt.

The bottle design must have the following text on it:
Main Text: Love them both
Paragraph text: Our ministry’s aim is to not only save unborn babies, but to provide love, support, and life-saving resources for vulnerable women in our community. By filling this bottle with cash, checks, and spare coins and returning it on collection day, you are truly saving and changing lives!
Optional text: Thank you!

We are including an example file and a template file. You do NOT have to use the template - but your file has to be the exact size mentioned. If you don't design as well as our sample, please don't waste our time by spamming us with hundreds of designs. We will ban design houses that spam us with designs that are more layouts (and not well designed).

Please note - white is a color. You don't have to do a box - but anything you don't make white will be see-through.

We will take the winners of this contest to a survey with the customers. We may choose two and edit the text of one slightly to be different. We must know the fonts used.

No gradients unless they are half-toned with relatively big sized dots.

Target Market(s)

Church Attendees coming from a Pregnancy Center

Industry/Entity Type

Religious Christian Churches

Requirements
Must have
• Professional, great palette, wording as described.
Nice to have
• Integrated design across the whole space with areas for text (no text all the way across)
Should not have
• Cartoon figures; elements shoved together that don't go together (i.e. - actually design something)

```html
<!DOCTYPE html>
<html lang="en">
<head>
<meta charset="utf-8">
<title>Love Them Both – Baby Bottle Bank Label</title>
<link rel="stylesheet" href="https://fonts.googleapis.com/css2?family=Ultra&family=PT+Sans+Narrow:wght@400;700&display=swap">
<style>
  :root {
    --canvas-bg: #f2f2f3;
    --label-white: #ffffff;
    --love-pink: #e8506e;
    --them-blue: #2ea3d8;
    --thanks-teal: #1f9a99;
    --body-grey: #6a6a6a;
    --photo-pink: #f3d3d6;
    --photo-skin: #e6b7a6;
    --accent-blue: #cfe6f3;
    --accent-yellow: #f6e3a6;
  }
  * { margin: 0; padding: 0; box-sizing: border-box; }
  html, body {
    width: 1200px;
    height: 1200px;
    overflow: hidden;
    background: var(--canvas-bg);
  }
  .canvas {
    position: relative;
    width: 1200px;
    height: 1200px;
    display: flex;
    align-items: center;
    justify-content: center;
  }
  .bottle-label {
    position: relative;
    width: 1120px;
    height: 601px;
    background: var(--label-white);
    overflow: hidden;
    box-shadow: 0 6px 24px rgba(0,0,0,0.08);
  }
  .photo-area {
    position: absolute;
    left: 0;
    top: 0;
    width: 520px;
    height: 601px;
    background:
      radial-gradient(ellipse at 62% 68%, var(--photo-skin) 0%, rgba(230,183,166,0.55) 28%, rgba(243,211,214,0.6) 55%, rgba(255,255,255,0) 85%),
      linear-gradient(90deg, var(--photo-pink) 0%, #f7e4e6 70%, var(--label-white) 100%);
  }
  .decor-star {
    position: absolute;
    border-radius: 28%;
  }
  .decor-star--blue {
    right: 34px;
    top: 60px;
    width: 88px;
    height: 88px;
    background: var(--accent-blue);
  }
  .decor-star--yellow {
    right: 40px;
    bottom: 52px;
    width: 74px;
    height: 74px;
    background: var(--accent-yellow);
  }
  .message {
    position: absolute;
    left: 560px;
    top: 58px;
    width: 440px;
  }
  .headline-love {
    font-family: "Ultra", serif;
    font-size: 124px;
    line-height: 1;
    color: var(--love-pink);
    letter-spacing: 1px;
  }
  .headline-them {
    font-family: "Ultra", serif;
    font-size: 66px;
    line-height: 1;
    color: var(--them-blue);
    margin-top: 6px;
    margin-left: 4px;
  }
  .mission {
    font-family: "PT Sans Narrow", sans-serif;
    font-size: 27px;
    line-height: 1.42;
    color: var(--body-grey);
    margin-top: 34px;
  }
  .thanks {
    font-family: "Ultra", serif;
    font-size: 46px;
    line-height: 1;
    color: var(--thanks-teal);
    margin-top: 40px;
  }
</style>
</head>
<body>
  <main class="canvas">
    <section class="bottle-label">
      <div class="photo-area" role="img" aria-label="Soft photograph of an adult hand gently holding a baby's tiny hand on a pale pink blanket, with small pink flowers"></div>

      <div class="decor-star decor-star--blue" role="img" aria-label="Small pale blue star decoration"></div>
      <div class="decor-star decor-star--yellow" role="img" aria-label="Small pale yellow star decoration"></div>

      <div class="message">
        <h1 class="headline-love">Love</h1>
        <h2 class="headline-them">them both</h2>
        <p class="mission">Our ministry’s aim is to not only save unborn babies, but to provide love, support, and life-saving resources for vulnerable women in our community. By filling this bottle with cash, checks, and spare coins and returning it on collection day, you are truly saving and changing lives!</p>
        <p class="thanks">Thank you!</p>
      </div>
    </section>
  </main>
</body>
</html>
```